Tideline Coach website development

Need a website designed for a coaching business. Very high-end, luxury, professionalism, in the area of STRESS, see brief attached. I have a logo already
Updates

Slow in providing feedback

Target Market(s)

CEOs very successful men and wealthy females, high end luxury market

Industry/Entity Type

coaching

Number of Pages Required

1 page

Requirements
Must have
• Luxury look, professional, serious but warm, appealing to both sexes

```html
<!DOCTYPE html>
<html lang="en">
<head>
<meta charset="UTF-8">
<title>Tideline Coach</title>
<link rel="stylesheet" href="https://fonts.googleapis.com/css2?family=Montserrat:wght@400;500;600&family=Lato:wght@400;700&family=Roboto:wght@400&display=swap">
<style>
:root{
  --navy:#2f4560;
  --navy-deep:#1c2a3d;
  --ink:#3a4656;
  --text:#444b54;
  --paper:#f6f6f6;
  --white:#ffffff;
  --butter:#fbf7a4;
  --butter-ink:#6b6a1e;
  --sky-top:#bfe0e8;
  --sky-low:#f4f6f6;
  --sea:#6f9fb0;
}
*{margin:0;padding:0;box-sizing:border-box}
html,body{width:1200px;height:3305px;overflow:hidden;background:var(--paper)}
body{position:relative;font-family:"Lato",sans-serif;color:var(--text)}
.abs{position:absolute}
.photo{position:absolute}

/* header */
.site-header{left:0;top:0;width:1200px;height:83px;background:var(--navy)}
.brand{left:50px;top:22px;font-family:"Montserrat",sans-serif;font-weight:500;font-size:31px;letter-spacing:3px;color:var(--white);display:flex;align-items:center;gap:12px}
.brand-dot{width:28px;height:28px;border-radius:50%;background:var(--white)}
.contact-link{top:31px;font-family:"Montserrat",sans-serif;font-weight:600;font-size:15px;color:var(--white);display:flex;align-items:center;gap:7px}

/* hero */
.hero{left:0;top:83px;width:1200px;height:584px;background:linear-gradient(180deg,var(--sky-top) 0%,#dbecef 40%,var(--sky-low) 72%)}
.hero-sea{left:0;top:517px;width:1200px;height:150px;background:linear-gradient(180deg,#5d8ea3 0%,#7eaab9 45%,#c9dde3 75%,#e6eef0 100%)}
.rule{background:var(--navy);height:2px}
.hero-welcome{left:272px;top:214px;width:657px;text-align:center;font-family:"Montserrat",sans-serif;font-size:31px;color:var(--navy)}
.hero-title{left:272px;top:258px;width:657px;text-align:center;font-family:"Montserrat",sans-serif;font-size:55px;letter-spacing:1px;color:var(--navy)}
.hero-lead{left:272px;top:341px;width:657px;text-align:center;font-size:14.5px;line-height:19px;color:#4a4f55}
.btn{background:var(--butter);color:var(--butter-ink);font-family:"Montserrat",sans-serif;font-weight:500;font-size:13px;display:flex;align-items:center;justify-content:center;box-shadow:0 2px 6px rgba(0,0,0,.12)}

/* about */
.about-title{left:503px;top:804px;font-family:"Montserrat",sans-serif;font-size:30px;color:var(--navy)}
.about-text{left:503px;top:887px;width:680px;font-size:15.5px;line-height:20px;color:var(--text)}
.about-sign{left:503px;top:983px;font-size:14.5px;color:var(--text)}

/* stats band */
.band{left:0;top:1238px;width:1200px;height:418px;background:var(--navy-deep)}
.band-text{left:637px;top:1390px;width:540px;font-size:23px;line-height:28px;color:var(--white)}

/* help */
.help-heading{left:0;top:1740px;width:1200px;text-align:center;font-size:20px;color:var(--ink)}
.help-label{top:2078px;width:270px;text-align:center;font-size:16px;color:var(--ink)}

/* perspective */
.perspective{left:0;top:2182px;width:1200px;height:417px;background:#fbfaf8}
.perspective-text{left:552px;top:2327px;width:570px;font-family:"Roboto",sans-serif;font-size:23.5px;line-height:28px;color:#3b3f45}

/* cta */
.cta{left:127px;top:2682px;width:946px;height:331px;background:var(--navy)}
.cta-note{left:127px;top:2740px;width:946px;text-align:center;font-family:"Roboto",sans-serif;font-size:13.5px;line-height:17px;color:var(--white)}
.cta-bar{left:517px;top:2787px;width:166px;height:4px;background:var(--white);border-radius:2px}
.cta-question{left:127px;top:2835px;width:946px;text-align:center;font-family:"Roboto",sans-serif;font-size:23px;color:var(--white)}
.field{top:2922px;width:249px;height:39px;background:var(--white);border-radius:3px;font-family:"Montserrat",sans-serif;font-size:13px;color:#8a8f96;padding-left:14px;display:flex;align-items:center}

/* footer */
.site-footer{left:0;top:3099px;width:1200px;height:206px;background:var(--white)}
.social{top:3131px;width:22px;height:22px;border-radius:50%;background:var(--navy-deep)}
.footer-line{left:0;width:1200px;text-align:center;font-family:"Roboto",sans-serif;font-size:14px;color:#4a4f55}
</style>
</head>
<body>

<header class="abs site-header">
  <div class="abs brand"><span class="brand-dot"></span>TIDELINE COACH</div>
  <div class="abs contact-link" style="left:886px">
    <svg width="12" height="14" viewBox="0 0 12 14"><path d="M3 1 L5 4 L3.8 5.5 C4.6 7.5 6 9 8 10 L9.5 8.8 L12 11 L10.5 13 C5 12 1 7 1.5 2 Z" fill="#fff"/></svg>
    (555) 014-2290
  </div>
  <div class="abs contact-link" style="left:1046px">
    <svg width="17" height="13" viewBox="0 0 17 13"><rect x="0" y="0" width="17" height="13" rx="1.5" fill="#fff"/><path d="M1 1.5 L8.5 7 L16 1.5" stroke="#2f4560" stroke-width="1.6" fill="none"/></svg>
    E-mail Us
  </div>
</header>

<section class="abs hero" role="img" aria-label="Calm sky over the open sea"></section>
<div class="abs hero-sea" role="img" aria-label="Gentle ocean waves rolling to shore"></div>
<div class="abs rule" style="left:272px;top:228px;width:217px"></div>
<div class="abs rule" style="left:272px;top:236px;width:217px"></div>
<div class="abs rule" style="left:712px;top:228px;width:217px"></div>
<div class="abs rule" style="left:712px;top:236px;width:217px"></div>
<div class="abs hero-welcome">Welcome to</div>
<h1 class="abs hero-title" style="font-weight:400">TIDELINE COACH</h1>
<div class="abs rule" style="left:272px;top:329px;width:657px"></div>
<p class="abs hero-lead">Recognize your stressors and control them. When we sense it’s coming<br>we can deal with it, resolve it, or use it to our advantage.</p>
<div class="abs btn" style="left:466px;top:393px;width:268px;height:36px">SCHEDULE AN APPOINTMENT</div>
<div class="abs rule" style="left:272px;top:444px;width:657px;height:3px"></div>

<section class="about">
  <div class="abs" style="left:296px;top:960px;width:136px;height:169px;background:var(--navy-deep);border-radius:8px"></div>
  <div class="photo" role="img" aria-label="Portrait of the coach in a red suit seated outdoors" style="left:144px;top:778px;width:267px;height:332px;border-radius:8px;background:linear-gradient(160deg,#5a5440 0%,#3d3a2c 45%,#b8262a 70%,#4a4232 100%)"></div>
  <h2 class="abs about-title" style="font-weight:400">Tideline Coach</h2>
  <div class="abs" style="left:504px;top:845px;width:67px;height:5px;background:var(--navy-deep);border-radius:3px"></div>
  <p class="abs about-text">Tideline Coach came about due to my desire to help people lead a better and healthier life. Initially, I was involved in the fitness/body side of health. As years passed and my experience grew, I realized how important the mind was in total wellness, and that the mind is all powerful and controlling. Control the mind, control the body and achieve success.</p>
  <p class="abs about-sign">-Elena Ward, Owner</p>
</section>

<section class="abs band"></section>
<div class="photo" role="img" aria-label="Black and white photo of a person working at a laptop" style="left:46px;top:1277px;width:200px;height:249px;background:linear-gradient(135deg,#e8e8e8,#8c8c8c 60%,#3c3c3c)"></div>
<div class="photo" role="img" aria-label="Hands typing on a laptop keyboard" style="left:216px;top:1377px;width:199px;height:249px;background:linear-gradient(160deg,#e2ddd4 0%,#b98a45 45%,#4a3a2a 100%)"></div>
<div class="photo" role="img" aria-label="Busy open-plan office full of workers" style="left:389px;top:1277px;width:200px;height:249px;background:linear-gradient(180deg,#2a2a2a 0%,#8a8d90 45%,#4f5357 100%)"></div>
<p class="abs band-text">Stress can be the most debilating factor in our lives, it is the root cause of so many diseases and costs the US workplace an estimated 300 billion dollars due to loss of productivity.</p>

<section class="help">
  <h3 class="abs help-heading" style="font-weight:400">Tideline coach will help you to :</h3>
  <div class="photo" role="img" aria-label="Two people talking across a café table" style="left:234px;top:1815px;width:200px;height:250px;background:linear-gradient(160deg,#8a6a4a,#c9b69a 45%,#3e4a3a)"></div>
  <div class="photo" role="img" aria-label="Hands cupping a glowing light bulb in the dark" style="left:500px;top:1815px;width:200px;height:250px;background:radial-gradient(circle at 52% 52%,#f5a640 0%,#8a4a1a 25%,#1a1410 60%)"></div>
  <div class="photo" role="img" aria-label="Portrait of a smiling man against a dark background" style="left:767px;top:1815px;width:200px;height:250px;background:radial-gradient(circle at 50% 40%,#9a6a4a 0%,#4a3024 35%,#141414 75%)"></div>
  <p class="abs help-label" style="left:199px">recognize your stressors</p>
  <p class="abs help-label" style="left:465px">control them</p>
  <p class="abs help-label" style="left:732px">deal with it to your advantage</p>
</section>

<section class="abs perspective"></section>
<div class="photo" role="img" aria-label="Smiling man on a phone call at a café" style="left:0;top:2182px;width:255px;height:417px;background:linear-gradient(160deg,#c9b08a 0%,#efe6da 45%,#b88a5a 100%)"></div>
<div class="photo" role="img" aria-label="Man with headphones working in a café" style="left:255px;top:2182px;width:242px;height:119px;background:linear-gradient(135deg,#3a3a34,#b8b0a0 60%,#6a5a4a)"></div>
<div class="photo" role="img" aria-label="Person working on a laptop" style="left:255px;top:2301px;width:100px;height:150px;background:linear-gradient(160deg,#c8ccd0,#2a3a4a)"></div>
<div class="photo" role="img" aria-label="Woman smiling at a laptop" style="left:355px;top:2301px;width:142px;height:150px;background:linear-gradient(160deg,#e9e6e0,#b86a4a 60%,#6a5a50)"></div>
<div class="photo" role="img" aria-label="Woman smiling at a desk by the window" style="left:255px;top:2451px;width:242px;height:148px;background:linear-gradient(135deg,#3a3430,#cfc8bc 55%,#8a9aa8)"></div>
<p class="abs perspective-text">Stress is not all bad, and since we are surrounded by engulfed by stress, or it isn’t going anywhere soon, we need to deal with it, and even better, channel to be an advantage/tool to perform better.</p>

<section class="abs cta"></section>
<p class="abs cta-note">Effective stress control and problem solving skills may be the only thing that will keep your head above<br>water in the next decade. It really is becoming quite serious and so should be taken very seriously.</p>
<div class="abs cta-bar"></div>
<h3 class="abs cta-question" style="font-weight:400">What is your plan for the next decade? Or, will you just let stress win?</h3>
<div class="abs field" style="left:200px">Name</div>
<div class="abs field" style="left:467px">E-mail</div>
<div class="abs btn" style="left:734px;top:2922px;width:266px;height:39px;box-shadow:none;border:1px solid #e6e08a">SCHEDULE AN APPOINTMENT</div>

<footer class="abs site-footer">
</footer>
<div class="abs social" style="left:528px" aria-label="Social link"></div>
<div class="abs social" style="left:572px" aria-label="Social link"></div>
<div class="abs social" style="left:615px" aria-label="Social link"></div>
<div class="abs social" style="left:654px" aria-label="Social link"></div>
<p class="abs footer-line" style="top:3188px">2270 Harbor Lane, Suite B</p>
<p class="abs footer-line" style="top:3224px">Seaview, CA 90417</p>
<p class="abs footer-line" style="top:3257px">(555) 014-2290</p>

</body>
</html>
```